Tech business card design

We need an amazing business card design for our new business 'Pexla' a marketing tech startup based in Sydney, Australia. We provide an online marketplace for businesses to search and buy advertising media, connect with service providers and learn more about marketing. We wish to communicate 'cool tech', reliability and professionalism and design based around our logo.

Target Market(s)

Business Owners

Contact Information for Business Card

Name
Position
Email Address
Website
Phone Number

Font styles to use
Other font styles liked:
• Avenir & Avenir Next

Colors

Designer to choose colors to be used in the design.

```html
<!DOCTYPE html>
<html lang="en">
<head>
<meta charset="utf-8">
<title>Pexla Business Card</title>
<link rel="stylesheet" href="https://fonts.googleapis.com/css2?family=Mulish:wght@400;700;900&display=swap">
<style>
  :root {
    --navy: #15133f;
    --white: #ffffff;
    --ink: #2a2a33;
    --backdrop: #e6e8eb;
    --rule: #6b6b78;
  }
  * { margin: 0; padding: 0; box-sizing: border-box; }
  html, body {
    width: 1200px;
    height: 900px;
    overflow: hidden;
    background: var(--backdrop);
    font-family: "Mulish", "Avenir Next", Avenir, sans-serif;
  }
  .card-sheet {
    position: relative;
    width: 1200px;
    height: 900px;
  }
  .card {
    position: absolute;
    left: 290px;
    width: 620px;
    height: 379px;
    overflow: hidden;
    border-radius: 3px;
    box-shadow: 0 10px 26px rgba(20, 20, 50, 0.18);
  }
  .card--front { top: 50px; }
  .card--back  { top: 471px; }
  .card-art {
    position: absolute;
    inset: 0;
    width: 100%;
    height: 100%;
  }
  .wordmark {
    position: absolute;
    font-weight: 900;
    letter-spacing: -1px;
    line-height: 1;
  }
  .card--front .wordmark {
    left: 200px;
    top: 140px;
    font-size: 84px;
    color: var(--white);
  }
  .front-url {
    position: absolute;
    left: 206px;
    top: 232px;
    font-size: 17px;
    letter-spacing: 0.6px;
    color: var(--white);
  }
  .card--back .wordmark {
    left: 318px;
    top: 62px;
    font-size: 56px;
    color: var(--navy);
  }
  .contact {
    position: absolute;
    left: 152px;
    top: 222px;
    color: var(--ink);
  }
  .contact-name {
    font-size: 18px;
    font-weight: 700;
    color: var(--navy);
  }
  .contact-role {
    font-size: 13px;
    margin-top: 2px;
    color: var(--rule);
  }
  .contact-rule {
    width: 112px;
    height: 1px;
    background: var(--rule);
    margin: 9px 0 10px;
  }
  .contact-list { list-style: none; }
  .contact-list li {
    display: flex;
    align-items: center;
    gap: 9px;
    font-size: 15px;
    line-height: 24px;
  }
  .contact-icon { width: 15px; height: 15px; flex: none; }
</style>
</head>
<body>
<main class="card-sheet">

  <section class="card card--front" aria-label="Business card front">
    <svg class="card-art" viewBox="0 0 620 379" aria-hidden="true">
      <rect width="620" height="379" fill="var(--navy)"/>
      <polygon points="0,40 0,379 135,379" fill="var(--white)"/>
      <polygon points="480,0 620,0 620,339" fill="var(--white)"/>
      <g stroke="var(--navy)" stroke-width="3">
        <line x1="4" y1="200" x2="56" y2="360"/>
        <line x1="4" y1="236" x2="44" y2="358"/>
        <line x1="4" y1="272" x2="32" y2="356"/>
        <line x1="568" y1="24" x2="614" y2="166"/>
        <line x1="580" y1="20" x2="614" y2="124"/>
        <line x1="592" y1="16" x2="614" y2="84"/>
      </g>
    </svg>
    <div class="wordmark">pexla</div>
    <div class="front-url">www.pexlamedia.com.au</div>
  </section>

  <section class="card card--back" aria-label="Business card back">
    <svg class="card-art" viewBox="0 0 620 379" aria-hidden="true">
      <rect width="620" height="379" fill="var(--white)"/>
      <polygon points="0,40 0,379 135,379" fill="var(--navy)"/>
      <polygon points="480,0 620,0 620,339" fill="var(--navy)"/>
      <g stroke="var(--navy)" stroke-width="3">
        <line x1="70" y1="150" x2="126" y2="290"/>
        <line x1="82" y1="150" x2="130" y2="270"/>
        <line x1="94" y1="150" x2="134" y2="250"/>
        <line x1="526" y1="150" x2="588" y2="300"/>
        <line x1="514" y1="160" x2="564" y2="280"/>
        <line x1="502" y1="170" x2="539" y2="260"/>
      </g>
    </svg>
    <div class="wordmark">pexla</div>
    <div class="contact">
      <div class="contact-name">Marcus Reed</div>
      <div class="contact-role">Founder | Director</div>
      <div class="contact-rule"></div>
      <ul class="contact-list">
        <li>
          <svg class="contact-icon" viewBox="0 0 16 16" aria-hidden="true">
            <rect x="4" y="1" width="8" height="14" rx="1.5" fill="none" stroke="var(--navy)" stroke-width="1.5"/>
            <line x1="7" y1="12.5" x2="9" y2="12.5" stroke="var(--navy)" stroke-width="1.5"/>
          </svg>
          +61 (0)400 555 218
        </li>
        <li>
          <svg class="contact-icon" viewBox="0 0 16 16" aria-hidden="true">
            <rect x="1" y="3" width="14" height="10" fill="var(--navy)"/>
            <polyline points="1,3 8,9 15,3" fill="none" stroke="var(--white)" stroke-width="1.3"/>
          </svg>
          marcus@pexlamedia.com.au
        </li>
        <li>
          <svg class="contact-icon" viewBox="0 0 16 16" aria-hidden="true">
            <circle cx="8" cy="8" r="7" fill="var(--navy)"/>
            <ellipse cx="8" cy="8" rx="3" ry="7" fill="none" stroke="var(--white)" stroke-width="1"/>
            <line x1="1" y1="8" x2="15" y2="8" stroke="var(--white)" stroke-width="1"/>
          </svg>
          www.pexlamedia.com.au
        </li>
      </ul>
    </div>
  </section>

</main>
</body>
</html>
```